Professional Sales Business looking for inspirational poster

I need an inspirational poster design for sales professionals, targeted around the phrase "Win Fast, Lose Fast". The style of the poster will be primarily minimalistic and flat with the main focus being on the phrase, however, any graphics or creative font and background styles are encouraged. Color choice is up to you.

Design Specs:
Vector files are best. If creating a vector file isn't possible, 150dpi raster images (at actual size or bigger) are good too. The poster must be in a portrait layout and scalable to the sizes of 18" X 24" and 24" X 36". Please convert all text to outlines.

Please msg me if you have any additional questions.

```html
<!DOCTYPE html>
<html lang="en">
<head>
<meta charset="UTF-8">
<title>Win Fast Lose Fast – Poster</title>
<link rel="stylesheet" href="https://fonts.googleapis.com/css2?family=Arimo:wght@400;700&display=swap">
<style>
  :root {
    --canvas: #ececec;
    --paper-light: #f4f4f4;
    --paper-edge: #d9d9d9;
    --ink: #4a4a4a;
    --ink-soft: #5a5a5a;
    --gauge-light: #e2e2e2;
    --gauge-mid: #b9b9b9;
    --accent: #d81b60;
  }
  html, body {
    margin: 0;
    padding: 0;
    width: 1200px;
    height: 900px;
    overflow: hidden;
    background: var(--canvas);
    font-family: "Arimo", Arial, sans-serif;
  }
  .poster {
    position: absolute;
    left: 285px;
    top: 30px;
    width: 630px;
    height: 840px;
    background: radial-gradient(ellipse at 50% 45%, var(--paper-light) 0%, #ebebeb 55%, var(--paper-edge) 100%);
    color: var(--ink);
  }
  .gauge-cluster {
    position: absolute;
    left: 180px;
    top: 95px;
    width: 270px;
    height: 112px;
    display: flex;
    justify-content: space-between;
    overflow: hidden;
  }
  .gauge-dial {
    width: 128px;
    height: 128px;
    border-radius: 50%;
    background: radial-gradient(circle at 50% 50%, var(--gauge-light) 0%, var(--gauge-mid) 100%);
  }
  .dash-rule {
    position: absolute;
    left: 180px;
    top: 206px;
    width: 270px;
    height: 8px;
    border-top: 1.2px solid var(--ink);
    box-sizing: border-box;
  }
  .dash-rule::after {
    content: "";
    position: absolute;
    left: 0;
    right: 0;
    top: 5px;
    border-top: 1.5px dashed var(--ink);
  }
  .slogan {
    position: absolute;
    left: 0;
    right: 0;
    top: 224px;
    margin: 0;
    text-align: center;
    font-weight: 700;
    font-size: 100px;
    line-height: 86px;
    color: var(--ink);
  }
  .slogan span { display: block; }
  .slogan .word-win  { letter-spacing: 9px; margin-right: -9px; font-size: 106px; }
  .slogan .word-fast { letter-spacing: 3px; margin-right: -3px; }
  .slogan .word-lose { letter-spacing: -1px; margin-right: 1px; }
  .fuel-gauge {
    position: absolute;
    left: 283px;
    top: 588px;
    width: 64px;
    height: 34px;
    border-radius: 32px 32px 0 0;
    background: radial-gradient(circle at 50% 100%, var(--gauge-light) 0%, var(--gauge-mid) 100%);
  }
  .refuel-label {
    position: absolute;
    left: 0;
    right: 0;
    top: 632px;
    text-align: center;
    font-weight: 700;
    font-size: 13px;
    letter-spacing: 0.5px;
    color: var(--accent);
  }
  .logo-placeholder {
    position: absolute;
    left: 0;
    right: 0;
    top: 735px;
    text-align: center;
    font-weight: 400;
    font-size: 14px;
    color: var(--ink-soft);
  }
</style>
</head>
<body>
  <main class="poster">
    <div class="gauge-cluster">
      <div class="gauge-dial" role="img" aria-label="Speedometer dial showing high speed"></div>
      <div class="gauge-dial" role="img" aria-label="Tachometer dial showing high revs"></div>
    </div>
    <div class="dash-rule"></div>

    <h1 class="slogan">
      <span class="word-win">WIN</span>
      <span class="word-fast">FAST</span>
      <span class="word-lose">LOSE</span>
      <span class="word-fast">FAST</span>
    </h1>

    <div class="fuel-gauge" role="img" aria-label="Fuel gauge near empty"></div>
    <div class="refuel-label">REFUEL</div>

    <div class="logo-placeholder">logo will be here</div>
  </main>
</body>
</html>
```